Business card design Needed for new logo / Construction business, home extensions and new builds

We need a business card design using our new logo files which i will attach to this project :)

We are a small construction business specialising in home extensions, new builds and property development. We are very ambitious and would appreciate professional and elegant designs for our new business card.

Very serious about using the services on MakerQuarry and recently acquired our new logo from here :)

Please get involved, i will feedback when i can as i am very busy but can respond daily, thanks

Target Market(s)

People that want to build onto their houses, new building developments or adding too their existing property

Industry/Entity Type

Construction

Contact Information for Business Card

Renwick Tolliver Construction, Lionel Ashby (Managing Director), Tel 07822254961, email - info@renwick-tolliver, www.renwick-tolliver.co.uk

Colors

Designer to choose colors to be used in the design.

Requirements
Must have
• I like a deep grey on the back please. A lot of you have provided black from and back, try mixing things up a little. The black looks cool 😎 Thanks

```html
<!DOCTYPE html>
<html lang="en">
<head>
<meta charset="utf-8">
<title>Renwick Tolliver Construction – Business Card</title>
<link rel="stylesheet" href="https://fonts.googleapis.com/css2?family=Open+Sans:wght@400;600;700&display=swap">
<style>
  :root {
    --backdrop: #2b2b2f;
    --card: #1f1f23;
    --card-back: #232327;
    --back-mark: #34343a;
    --gold-light: #f3c860;
    --gold: #d99a22;
    --gold-dark: #a8700f;
    --silver: #d6d6d8;
    --silver-dark: #8e8e92;
    --text: #f2f2f2;
    --divider: #8a8a8e;
  }
  * { box-sizing: border-box; margin: 0; padding: 0; }
  html, body {
    width: 1200px; height: 780px; overflow: hidden;
    background: var(--backdrop);
    font-family: "Open Sans", Arial, sans-serif;
  }
  .canvas { position: relative; width: 1200px; height: 780px; }
  .card {
    position: absolute; top: 222px; width: 520px; height: 336px;
    border-radius: 4px; overflow: hidden;
  }
  .card--front { left: 50px; background: var(--card); }
  .card--back { left: 630px; background: var(--card-back); }

  /* front */
  .brand {
    position: absolute; left: 30px; top: 88px; width: 180px;
    text-align: center; color: var(--silver);
    font-weight: 600; font-size: 17px; line-height: 1.3; letter-spacing: 0.06em;
    text-transform: uppercase;
  }
  .brand__square {
    display: block; width: 14px; height: 14px; margin: 0 auto 10px;
    background: var(--gold);
  }
  .divider {
    position: absolute; left: 232px; top: 36px; width: 1px; height: 176px;
    background: linear-gradient(to bottom, transparent, var(--divider) 20%, var(--divider) 80%, transparent);
  }
  .person { position: absolute; left: 262px; top: 62px; }
  .person__name { font-size: 27px; font-weight: 700; line-height: 1.1; }
  .person__first { color: var(--silver); }
  .person__last { color: var(--gold); }
  .person__role { color: var(--text); font-size: 14px; margin-top: 2px; }
  .contacts { list-style: none; margin-top: 22px; }
  .contacts li {
    display: flex; align-items: center; gap: 8px;
    color: var(--text); font-size: 14px; line-height: 21px;
  }
  .contacts svg { width: 12px; height: 12px; flex: none; }

  .address-band {
    position: absolute; left: 0; right: 0; top: 262px; height: 36px;
    display: flex;
  }
  .address-band__gold {
    flex: 1; display: flex; align-items: center; padding-left: 34px;
    background: linear-gradient(to bottom, var(--gold-light), var(--gold) 55%, var(--gold-dark));
    color: #fff; font-size: 13px; font-weight: 600;
  }
  .address-band__silver {
    width: 70px;
    background: linear-gradient(to bottom, #f0f0f2, var(--silver) 50%, var(--silver-dark));
  }

  /* back */
  .back-brand {
    position: absolute; inset: 0; display: flex; flex-direction: column;
    align-items: center; justify-content: center; gap: 12px;
    color: var(--back-mark); font-weight: 700; font-size: 26px;
    letter-spacing: 0.06em; text-transform: uppercase; text-align: center; line-height: 1.25;
  }
  .back-brand__square { width: 22px; height: 22px; background: var(--back-mark); }
</style>
</head>
<body>
<main class="canvas">
  <section class="card card--front" aria-label="Business card front">
    <div class="brand">
      <span class="brand__square"></span>
      Renwick Tolliver Construction
    </div>
    <div class="divider"></div>
    <div class="person">
      <h1 class="person__name"><span class="person__first">Lionel</span> <span class="person__last">Ashby</span></h1>
      <p class="person__role">Managing Director</p>
      <ul class="contacts">
        <li>
          <svg viewBox="0 0 24 24" fill="var(--gold)"><path d="M6.6 10.8a15.1 15.1 0 0 0 6.6 6.6l2.2-2.2a1 1 0 0 1 1-.25 11.4 11.4 0 0 0 3.6.57 1 1 0 0 1 1 1V20a1 1 0 0 1-1 1A17 17 0 0 1 3 4a1 1 0 0 1 1-1h3.5a1 1 0 0 1 1 1c0 1.25.2 2.45.57 3.6a1 1 0 0 1-.25 1z"/></svg>
          0782 225 4961
        </li>
        <li>
          <svg viewBox="0 0 24 24" fill="none" stroke="var(--gold)" stroke-width="2.4"><rect x="3" y="5" width="18" height="14" rx="1"/><path d="M3 6l9 7 9-7"/></svg>
          info@renwick-tolliver.co.uk
        </li>
        <li>
          <svg viewBox="0 0 24 24" fill="none" stroke="var(--gold)" stroke-width="2.2"><circle cx="12" cy="12" r="9"/><path d="M3 12h18M12 3c3 3 3 15 0 18M12 3c-3 3-3 15 0 18"/></svg>
          www.renwick-tolliver.co.uk
        </li>
      </ul>
    </div>
    <div class="address-band">
      <p class="address-band__gold">Hallow Lane, Westbury Fields, BH4 7QT</p>
      <div class="address-band__silver"></div>
    </div>
  </section>

  <section class="card card--back" aria-label="Business card back">
    <div class="back-brand">
      <span class="back-brand__square"></span>
      Renwick Tolliver<br>Construction
    </div>
  </section>
</main>
</body>
</html>
```